Bright Harbor Counseling Letterhead for hip modern business

I would like some ombre use of the colors in the logo hip letterhead that incorporates logo colors and feel, needs to connect with young professionals and college students. i need to be able to write letters to schools to excuse absences as well. i like color blocks on one side preferably using colors from the attached logo design.

Target Market(s)

high income young people, young adults and college students

Industry/Entity Type

mental health

Font styles to use
Serif
Sans Serif

Colors
0054AA
0677BA
7BADD7
CADEEF
E8F1F8
0094D4
00A9DD
6FCCEA
C7EBF8
E9F6FB
00AB8E
00BBA5
67D7C9
C6EFE9
E9F9F6
59FF00
82FF00
B8FF75
E3FFCB
F4FFEA
A7469A
B969AE
D3A5CF
EDDBEB
F8F0F9
6B429C
8869AF
B7A5CE
E3DAEB
F3F0F8

Requirements
Must have
• a modern hip feel, somewhat color

```html
<!DOCTYPE html>
<html lang="en">
<head>
<meta charset="utf-8">
<title>Bright Harbor Counseling Letterhead</title>
<link href="https://fonts.googleapis.com/css2?family=Open+Sans:wght@300;400;600&display=swap" rel="stylesheet">
<style>
  :root {
    --backdrop: #2f2f2f;
    --paper: #ffffff;
    --ink: #2b2b2b;
    --ink-soft: #444444;
    --brand-blue: #2f74c0;
    --brand-teal: #5cc8c0;
    --brand-purple: #93307f;
    --brand-sky: #3a8fd0;
  }
  html, body {
    margin: 0;
    width: 1200px;
    height: 962px;
    overflow: hidden;
    background: var(--backdrop);
    font-family: "Open Sans", Arial, sans-serif;
  }
  .letterhead {
    position: absolute;
    left: 282px;
    top: 31px;
    width: 636px;
    height: 900px;
    background: var(--paper);
    overflow: hidden;
  }
  .brand {
    position: absolute;
    left: 48px;
    top: 60px;
    display: flex;
    align-items: center;
    gap: 10px;
  }
  .brand-dot {
    width: 14px;
    height: 14px;
    border-radius: 50%;
    background: var(--brand-purple);
  }
  .brand-name {
    font-weight: 300;
    font-size: 22px;
    line-height: 1.1;
    color: var(--ink);
    letter-spacing: 0.3px;
  }
  .contact {
    position: absolute;
    right: 48px;
    top: 54px;
    font-style: normal;
    font-size: 9.5px;
    font-weight: 400;
    line-height: 1.45;
    color: var(--ink-soft);
  }
  .contact p { margin: 0; }
  .contact-line {
    display: flex;
    align-items: center;
    gap: 5px;
  }
  .contact-icon {
    width: 8px;
    height: 8px;
    border-radius: 50%;
    flex: none;
  }
  .contact-icon.phone { background: var(--brand-teal); }
  .contact-icon.fax { background: var(--brand-sky); }
  .contact-icon.email { background: var(--brand-purple); }
  .footer {
    position: absolute;
    left: 0;
    right: 0;
    bottom: 0;
  }
  .website {
    margin: 0 0 14px 48px;
    font-size: 12px;
    font-weight: 400;
    color: var(--brand-blue);
  }
  .color-bands {
    display: grid;
    grid-template-columns: 1fr 140px 200px;
    height: 28px;
  }
  .band-blue { background: var(--brand-blue); }
  .band-teal { background: var(--brand-teal); }
  .band-purple { background: var(--brand-purple); }
</style>
</head>
<body>
  <main class="letterhead">
    <header>
      <div class="brand">
        <span class="brand-dot"></span>
        <span class="brand-name">Bright Harbor Counseling</span>
      </div>
      <address class="contact">
        <p>Suite 210, 48 Harbor Lane,</p>
        <p>Portland, ME 04101</p>
        <p class="contact-line"><span class="contact-icon phone"></span>(207) 555 0142</p>
        <p class="contact-line"><span class="contact-icon fax"></span>(207) 555 0143</p>
        <p class="contact-line"><span class="contact-icon email"></span>hello@brightharbor.com</p>
      </address>
    </header>

    <footer class="footer">
      <p class="website">www.brightharborcounseling.com</p>
      <div class="color-bands" aria-hidden="true">
        <span class="band-blue"></span>
        <span class="band-teal"></span>
        <span class="band-purple"></span>
      </div>
    </footer>
  </main>
</body>
</html>
```